Dental Medical History Form - Content provided

Design a medical history form for a dental practice. Content is provided so all that is needed is the formatting to make it look great and easy to read.

"Patient Information" to include all information contained in top portion of the "Patient Medical History Form" docx file.

"Medical History" should follow the formatting and content of the "Exact Medical History" file as this is what the entry fields look like in our practice software and so we would like it to match.

1st page - Patient info, allergies, medications, antibiotics, joint replacement, pregnancy.

2nd page - Do you have, or have you had, any of the following? . . . . . . .
Updates

Target Market(s)

All ages but must be clear enough for elderly to read. Use as much space as possible to keep font size bigger yet keep to two pages

Industry/Entity Type

Dental

Font styles to use
Sans Serif

Requirements
Must have
• All content provided
• Our logo at the top (file provided)
• Century Gothic Font
• Limit to two pages

```html
<!DOCTYPE html>
<html lang="en">
<head>
<meta charset="utf-8">
<title>Harbour Dental – Confidential Medical History</title>
<link href="https://fonts.googleapis.com/css2?family=Didact+Gothic&display=swap" rel="stylesheet">
<style>
:root{
  --bg:#e2e2e2;
  --paper:#ffffff;
  --ink:#1a1a1a;
  --bar:#000000;
  --panel:#e4e4e4;
  --field:#ffffff;
  --soft:#ececec;
  --muted:#555555;
}
*{box-sizing:border-box;margin:0;padding:0}
html,body{width:1200px;height:1000px;overflow:hidden}
body{background:var(--bg);font-family:"Didact Gothic","Century Gothic",sans-serif;color:var(--ink);position:relative}
.page{position:absolute;top:110px;width:551px;height:780px;background:var(--paper);overflow:hidden}
.page-one{left:36px}
.page-two{left:617px}
.t{position:absolute;font-size:9.5px;line-height:12px;white-space:nowrap}
.b{font-weight:700}
.f{position:absolute;height:11px;background:var(--field)}
.g{position:absolute;height:12px;background:var(--soft)}
.box{display:inline-block;width:8px;height:8px;border:1px solid #333;vertical-align:-1px;margin-left:1px;background:#fff}
.brand{position:absolute;right:27px;top:30px;font-size:26px;line-height:30px;color:#333;display:flex;align-items:center;gap:6px}
.brand-mark{width:9px;height:9px;background:#333}
.address{position:absolute;right:27px;top:78px;text-align:right;font-size:9px;line-height:11px}
.tab{position:absolute;height:15px;background:var(--bar);color:#fff;font-size:10.5px;line-height:15px;padding-left:4px;white-space:nowrap}
.panel{position:absolute;background:var(--panel)}
.bar{position:absolute;left:26px;width:499px;height:15px;background:var(--bar);color:#fff;font-size:10.5px;line-height:15px;padding-left:5px;white-space:nowrap}
.bar svg{vertical-align:-2px}
.q{font-size:10.5px}
.digits{word-spacing:8px}
.col{position:absolute;top:0;left:0;width:260px;height:100%}
.col-right{left:252px}
.row{position:absolute;left:0;width:260px;height:12px;font-size:9px;line-height:12px}
.row span{white-space:nowrap}
.row .l{position:absolute;left:34px}
.row .y{position:absolute;left:201px}
.row .n{position:absolute;left:237px}
.head{position:absolute;left:34px;font-size:9px;line-height:12px;font-weight:700;white-space:nowrap}
.sign{position:absolute;font-size:8.5px;line-height:12px}
.line{position:absolute;height:1px;background:#777}
.thanks{position:absolute;left:0;width:100%;text-align:center;font-size:7px;line-height:8px;font-style:italic;color:var(--muted)}
</style>
</head>
<body>

<section class="page page-one">
  <div class="brand"><span class="brand-mark"></span><span>harbour dental</span></div>
  <div class="address">3.04/118 Coastal View Rd<br>Brookvale NSW 2100<br>(02) 49 555 010</div>

  <div class="tab" style="left:26px;top:117px;width:178px">CONFIDENTIAL MEDICAL HISTORY</div>
  <div class="panel" style="left:26px;top:132px;width:499px;height:168px"></div>

  <span class="t" style="left:36px;top:142px">Name:</span>
  <div class="f" style="left:71px;top:142px;width:63px"></div>
  <div class="f" style="left:137px;top:142px;width:65px"></div>
  <div class="f" style="left:205px;top:142px;width:64px"></div>
  <span class="t" style="left:35px;top:154px">Title</span>
  <span class="t" style="left:94px;top:154px">First</span>
  <span class="t" style="left:154px;top:154px">Middle</span>
  <span class="t" style="left:228px;top:154px">Last</span>
  <span class="t" style="left:36px;top:173px">Address:</span><div class="f" style="left:77px;top:173px;width:192px"></div>
  <span class="t" style="left:36px;top:191px">DOB:</span><div class="f" style="left:61px;top:191px;width:208px"></div>
  <span class="t" style="left:36px;top:208px">Email Address:</span><div class="f" style="left:103px;top:208px;width:166px"></div>
  <span class="t" style="left:36px;top:225px">Phone Number(s):</span><div class="f" style="left:129px;top:225px;width:140px"></div>
  <span class="t" style="left:84px;top:244px">Mobile:</span><div class="f" style="left:121px;top:244px;width:148px"></div>
  <span class="t" style="left:92px;top:262px">Work:</span><div class="f" style="left:121px;top:262px;width:148px"></div>
  <span class="t" style="left:88px;top:279px">Home:</span><div class="f" style="left:121px;top:279px;width:148px"></div>

  <span class="t b" style="left:279px;top:142px">GENERAL PRACTITIONER:</span>
  <span class="t" style="left:279px;top:157px">Name:</span><div class="f" style="left:309px;top:157px;width:205px"></div>
  <span class="t" style="left:279px;top:170px">Practice Name:</span><div class="f" style="left:347px;top:170px;width:167px"></div>
  <span class="t" style="left:279px;top:183px">Phone Number:</span><div class="f" style="left:347px;top:183px;width:167px"></div>
  <span class="t" style="left:279px;top:196px">Do you have a health fund with dental cover? <b>Yes</b> or <b>No</b></span>
  <span class="t" style="left:279px;top:208px">If so, what is the name of the fund?</span>
  <div class="f" style="left:279px;top:220px;width:235px"></div>
  <span class="t" style="left:279px;top:234px">Fund Number?</span><div class="f" style="left:344px;top:234px;width:170px"></div>
  <span class="t" style="left:279px;top:250px">Priority Number on card:</span>
  <span class="t b digits" style="left:395px;top:250px">0 1 2 3 4 5</span>
  <span class="t" style="left:279px;top:264px">Occupation:</span><div class="f" style="left:336px;top:264px;width:178px"></div>
  <span class="t" style="left:279px;top:279px">Referred by:</span><div class="f" style="left:336px;top:279px;width:178px"></div>

  <div class="bar" style="top:316px">Please indicate if you are allergic to any of the following
    <svg width="10" height="10" viewBox="0 0 10 10"><rect x="0.5" y="0.5" width="9" height="9" fill="none" stroke="#fff"/><path d="M2 5l2 2 4-5" fill="none" stroke="#fff" stroke-width="1.2"/></svg> ?</div>
  <span class="t" style="left:31px;top:335px">Aspirin<span class="box"></span></span>
  <span class="t" style="left:81px;top:335px">Codeine<span class="box"></span></span>
  <span class="t" style="left:142px;top:335px">Penicillin<span class="box"></span></span>
  <span class="t" style="left:201px;top:335px">Sulfites<span class="box"></span></span>
  <span class="t" style="left:254px;top:335px">Latex<span class="box"></span></span>
  <span class="t" style="left:300px;top:335px">Local<span class="box"></span></span>
  <span class="t" style="left:348px;top:335px">Anaesthetic<span class="box"></span></span>
  <span class="t" style="left:423px;top:335px">Lactose<span class="box"></span></span>
  <span class="t" style="left:481px;top:335px">Nickel<span class="box"></span></span>
  <span class="t" style="left:31px;top:354px">Other</span><div class="g" style="left:57px;top:354px;width:468px"></div>

  <div class="bar" style="top:393px">Are you currently taking, or have ever taken, any of the following medication
    <svg width="10" height="10" viewBox="0 0 10 10"><rect x="0.5" y="0.5" width="9" height="9" fill="none" stroke="#fff"/><path d="M2 5l2 2 4-5" fill="none" stroke="#fff" stroke-width="1.2"/></svg> ?</div>
  <span class="t" style="left:31px;top:411px">Asthma inhaler <span class="box"></span></span>
  <span class="t" style="left:132px;top:411px">Anti-epileptics<span class="box"></span></span>
  <span class="t" style="left:230px;top:411px">Anti-depressants<span class="box"></span></span>
  <span class="t" style="left:338px;top:411px">Blood Pressure<span class="box"></span></span>
  <span class="t" style="left:437px;top:411px">Blood Thinners <span class="box"></span></span>
  <span class="t" style="left:31px;top:430px">Bisphosphonates<span class="box"></span></span>
  <span class="t" style="left:132px;top:430px">Chemotherapy<span class="box"></span></span>
  <span class="t" style="left:230px;top:430px">Insulin<span class="box"></span></span>
  <span class="t" style="left:324px;top:430px">Immunosuppressants<span class="box"></span></span>
  <span class="t" style="left:435px;top:430px">Steroids<span class="box"></span></span>
  <span class="t" style="left:31px;top:449px">Oral Contraceptive <span class="box"></span></span>
  <span class="t" style="left:132px;top:449px">Other<span class="box"></span></span>

  <div class="bar" style="top:497px">Please specify medication name, dose, and frequency where possible:</div>
  <div class="g" style="left:31px;top:518px;width:160px"></div><div class="g" style="left:196px;top:518px;width:160px"></div><div class="g" style="left:361px;top:518px;width:160px"></div>
  <div class="g" style="left:31px;top:538px;width:160px"></div><div class="g" style="left:196px;top:538px;width:160px"></div><div class="g" style="left:361px;top:538px;width:160px"></div>
  <div class="g" style="left:31px;top:557px;width:160px"></div><div class="g" style="left:196px;top:557px;width:160px"></div><div class="g" style="left:361px;top:557px;width:160px"></div>

  <span class="t q" style="left:31px;top:596px"><b>Do you require antibiotic cover?</b>&nbsp; Yes<span class="box"></span>&nbsp; No<span class="box"></span></span>
  <span class="t q" style="left:31px;top:624px"><b>Have you had a joint replacement?</b>&nbsp; Yes<span class="box"></span>&nbsp; No<span class="box"></span></span>
  <span class="t q b" style="left:31px;top:651px">Women:</span>
  <span class="t q" style="left:31px;top:667px"><b>Are you pregnant?</b>&nbsp; Yes<span class="box"></span>&nbsp; No<span class="box"></span>&nbsp; <b>Possible or Breast Feeding?</b>&nbsp; Yes<span class="box"></span>&nbsp; No<span class="box"></span></span>
  <span class="t b" style="right:25px;top:733px">PLEASE TURN OVER</span>
</section>

<section class="page page-two">
  <div class="tab" style="left:28px;top:27px;width:240px;font-size:9px;padding-left:6px;font-weight:700">Do you have, or have you had, any of the following?</div>
  <div class="panel" style="left:24px;top:42px;width:501px;height:545px"></div>

  <div class="col">
    <span class="head" style="top:48px">Dental</span>
    <div class="row" style="top:60px"><span class="l">Acid Reflux</span><span class="y">Yes<span class="box"></span></span><span class="n">No<span class="box"></span></span></div>
    <div class="row" style="top:71px"><span class="l">Bad Breath/Taste</span><span class="y">Yes<span class="box"></span></span><span class="n">No<span class="box"></span></span></div>
    <div class="row" style="top:83px"><span class="l">Bleeding/Swollen/Sore Gums</span><span class="y">Yes<span class="box"></span></span><span class="n">No<span class="box"></span></span></div>
    <div class="row" style="top:95px"><span class="l">Blisters/Ulcers in Mouth</span><span class="y">Yes<span class="box"></span></span><span class="n">No<span class="box"></span></span></div>
    <div class="row" style="top:106px"><span class="l">Broken tooth/filling</span><span class="y">Yes<span class="box"></span></span><span class="n">No<span class="box"></span></span></div>
    <div class="row" style="top:118px"><span class="l">Burning tongue</span><span class="y">Yes<span class="box"></span></span><span class="n">No<span class="box"></span></span></div>
    <div class="row" style="top:130px"><span class="l">Dry mouth</span><span class="y">Yes<span class="box"></span></span><span class="n">No<span class="box"></span></span></div>
    <div class="row" style="top:142px"><span class="l">Food collection between teeth</span><span class="y">Yes<span class="box"></span></span><span class="n">No<span class="box"></span></span></div>
    <div class="row" style="top:153px"><span class="l">Grinding/clenching teeth (day/night)</span><span class="y">Yes<span class="box"></span></span><span class="n">No<span class="box"></span></span></div>
    <div class="row" style="top:165px"><span class="l">Loose teeth</span><span class="y">Yes<span class="box"></span></span><span class="n">No<span class="box"></span></span></div>
    <div class="row" style="top:177px"><span class="l">Crooked teeth</span><span class="y">Yes<span class="box"></span></span><span class="n">No<span class="box"></span></span></div>
    <div class="row" style="top:188px"><span class="l">Discoloured teeth</span><span class="y">Yes<span class="box"></span></span><span class="n">No<span class="box"></span></span></div>
    <div class="row" style="top:200px"><span class="l">Sensitivity to Hot/Cold</span><span class="y">Yes<span class="box"></span></span><span class="n">No<span class="box"></span></span></div>
    <div class="row" style="top:211px"><span class="l">Tooth pain when chewing</span><span class="y">Yes<span class="box"></span></span><span class="n">No<span class="box"></span></span></div>
    <div class="row" style="top:223px"><span class="l">Jaw pain/Fracture</span><span class="y">Yes<span class="box"></span></span><span class="n">No<span class="box"></span></span></div>
    <div class="row" style="top:235px"><span class="l">Orthodontic treatment/history</span><span class="y">Yes<span class="box"></span></span><span class="n">No<span class="box"></span></span></div>
    <div class="row" style="top:247px"><span class="l">Oral Cancer</span><span class="y">Yes<span class="box"></span></span><span class="n">No<span class="box"></span></span></div>

    <span class="head" style="top:273px">Diet/Lifestyle</span>
    <div class="row" style="top:285px"><span class="l" style="font-size:8px">Drink more than one glass alcohol per day</span><span class="y">Yes<span class="box"></span></span><span class="n">No<span class="box"></span></span></div>
    <div class="row" style="top:297px"><span class="l">Smoking</span><span class="y">Yes<span class="box"></span></span><span class="n">No<span class="box"></span></span></div>
    <div class="row" style="top:310px"><span class="l">Carbonated drinks</span><span class="y">Yes<span class="box"></span></span><span class="n">No<span class="box"></span></span></div>
    <div class="row" style="top:322px"><span class="l">Sugary foods</span><span class="y">Yes<span class="box"></span></span><span class="n">No<span class="box"></span></span></div>

    <span class="head" style="top:348px">Blood</span>
    <div class="row" style="top:361px"><span class="l">Anaemia</span><span class="y">Yes<span class="box"></span></span><span class="n">No<span class="box"></span></span></div>
    <div class="row" style="top:373px"><span class="l">Blood clots</span><span class="y">Yes<span class="box"></span></span><span class="n">No<span class="box"></span></span></div>
    <div class="row" style="top:385px"><span class="l">Leukemia</span><span class="y">Yes<span class="box"></span></span><span class="n">No<span class="box"></span></span></div>
    <div class="row" style="top:398px"><span class="l">Low platelets</span><span class="y">Yes<span class="box"></span></span><span class="n">No<span class="box"></span></span></div>
    <div class="row" style="top:410px"><span class="l">Lymphoma</span><span class="y">Yes<span class="box"></span></span><span class="n">No<span class="box"></span></span></div>
    <div class="row" style="top:423px"><span class="l">Haemophelia</span><span class="y">Yes<span class="box"></span></span><span class="n">No<span class="box"></span></span></div>

    <span class="head" style="top:449px">Chest</span>
    <div class="row" style="top:462px"><span class="l">Bronchitis</span><span class="y">Yes<span class="box"></span></span><span class="n">No<span class="box"></span></span></div>
    <div class="row" style="top:475px"><span class="l">Cystic Fibrosis</span><span class="y">Yes<span class="box"></span></span><span class="n">No<span class="box"></span></span></div>
    <div class="row" style="top:488px"><span class="l">Emphysema</span><span class="y">Yes<span class="box"></span></span><span class="n">No<span class="box"></span></span></div>
    <div class="row" style="top:501px"><span class="l">Pneumonia</span><span class="y">Yes<span class="box"></span></span><span class="n">No<span class="box"></span></span></div>

    <span class="head" style="top:527px">Infectious Disease</span>
    <div class="row" style="top:540px"><span class="l">Creutzfeldt-Jakob Disease</span><span class="y">Yes<span class="box"></span></span><span class="n">No<span class="box"></span></span></div>
    <div class="row" style="top:553px"><span class="l">Hepatitis A,B,C,D</span><span class="y">Yes<span class="box"></span></span><span class="n">No<span class="box"></span></span></div>
    <div class="row" style="top:567px"><span class="l">HIV/AIDS</span><span class="y">Yes<span class="box"></span></span><span class="n">No<span class="box"></span></span></div>
  </div>

  <div class="col col-right">
    <div class="row" style="top:49px"><span class="l">Influenza</span><span class="y" style="left:205px">Yes<span class="box"></span></span><span class="n" style="left:241px">No<span class="box"></span></span></div>
    <div class="row" style="top:62px"><span class="l">Shingles</span><span class="y" style="left:205px">Yes<span class="box"></span></span><span class="n" style="left:241px">No<span class="box"></span></span></div>
    <div class="row" style="top:75px"><span class="l">Tuberculosis</span><span class="y" style="left:205px">Yes<span class="box"></span></span><span class="n" style="left:241px">No<span class="box"></span></span></div>

    <span class="head" style="top:110px">Heart</span>
    <div class="row" style="top:121px"><span class="l">Angina</span><span class="y" style="left:205px">Yes<span class="box"></span></span><span class="n" style="left:241px">No<span class="box"></span></span></div>
    <div class="row" style="top:134px"><span class="l">Atrial Fibrillation</span><span class="y" style="left:205px">Yes<span class="box"></span></span><span class="n" style="left:241px">No<span class="box"></span></span></div>
    <div class="row" style="top:146px"><span class="l">Blood Pressure (High/Low)</span><span class="y" style="left:205px">Yes<span class="box"></span></span><span class="n" style="left:241px">No<span class="box"></span></span></div>
    <div class="row" style="top:158px"><span class="l">Congenital Heart Disease</span><span class="y" style="left:205px">Yes<span class="box"></span></span><span class="n" style="left:241px">No<span class="box"></span></span></div>
    <div class="row" style="top:171px"><span class="l">Heart attack</span><span class="y" style="left:205px">Yes<span class="box"></span></span><span class="n" style="left:241px">No<span class="box"></span></span></div>
    <div class="row" style="top:183px"><span class="l">Heart murmur</span><span class="y" style="left:205px">Yes<span class="box"></span></span><span class="n" style="left:241px">No<span class="box"></span></span></div>
    <div class="row" style="top:195px"><span class="l">Heart surgery</span><span class="y" style="left:205px">Yes<span class="box"></span></span><span class="n" style="left:241px">No<span class="box"></span></span></div>
    <div class="row" style="top:207px"><span class="l">Heart valve replacement</span><span class="y" style="left:205px">Yes<span class="box"></span></span><span class="n" style="left:241px">No<span class="box"></span></span></div>
    <div class="row" style="top:220px"><span class="l">Infective endocarditis</span><span class="y" style="left:205px">Yes<span class="box"></span></span><span class="n" style="left:241px">No<span class="box"></span></span></div>
    <div class="row" style="top:232px"><span class="l">Rheumatic Heart Disease</span><span class="y" style="left:205px">Yes<span class="box"></span></span><span class="n" style="left:241px">No<span class="box"></span></span></div>
    <div class="row" style="top:244px"><span class="l">Pacemaker</span><span class="y" style="left:205px">Yes<span class="box"></span></span><span class="n" style="left:241px">No<span class="box"></span></span></div>
    <div class="row" style="top:256px"><span class="l">Stent</span><span class="y" style="left:205px">Yes<span class="box"></span></span><span class="n" style="left:241px">No<span class="box"></span></span></div>

    <span class="head" style="top:288px">Other</span>
    <div class="row" style="top:299px"><span class="l">Anxiety/PTSD</span><span class="y" style="left:205px">Yes<span class="box"></span></span><span class="n" style="left:241px">No<span class="box"></span></span></div>
    <div class="row" style="top:311px"><span class="l">Arthritis</span><span class="y" style="left:205px">Yes<span class="box"></span></span><span class="n" style="left:241px">No<span class="box"></span></span></div>
    <div class="row" style="top:323px"><span class="l">Alzheimer's</span><span class="y" style="left:205px">Yes<span class="box"></span></span><span class="n" style="left:241px">No<span class="box"></span></span></div>
    <div class="row" style="top:335px"><span class="l">Asthma</span><span class="y" style="left:205px">Yes<span class="box"></span></span><span class="n" style="left:241px">No<span class="box"></span></span></div>
    <div class="row" style="top:347px"><span class="l">Anaphylaxis</span><span class="y" style="left:205px">Yes<span class="box"></span></span><span class="n" style="left:241px">No<span class="box"></span></span></div>
    <div class="row" style="top:359px"><span class="l">Auto-immune disease</span><span class="y" style="left:205px">Yes<span class="box"></span></span><span class="n" style="left:241px">No<span class="box"></span></span></div>
    <div class="row" style="top:371px"><span class="l">Coeliac</span><span class="y" style="left:205px">Yes<span class="box"></span></span><span class="n" style="left:241px">No<span class="box"></span></span></div>
    <div class="row" style="top:383px"><span class="l">Depression</span><span class="y" style="left:205px">Yes<span class="box"></span></span><span class="n" style="left:241px">No<span class="box"></span></span></div>
    <div class="row" style="top:394px"><span class="l">Diabetes</span><span class="y" style="left:205px">Yes<span class="box"></span></span><span class="n" style="left:241px">No<span class="box"></span></span></div>
    <div class="row" style="top:406px"><span class="l">Epilepsy</span><span class="y" style="left:205px">Yes<span class="box"></span></span><span class="n" style="left:241px">No<span class="box"></span></span></div>
    <div class="row" style="top:418px"><span class="l">Kidney Disease</span><span class="y" style="left:205px">Yes<span class="box"></span></span><span class="n" style="left:241px">No<span class="box"></span></span></div>
    <div class="row" style="top:430px"><span class="l">Liver Disease</span><span class="y" style="left:205px">Yes<span class="box"></span></span><span class="n" style="left:241px">No<span class="box"></span></span></div>
    <div class="row" style="top:442px"><span class="l">Osteoporosis</span><span class="y" style="left:205px">Yes<span class="box"></span></span><span class="n" style="left:241px">No<span class="box"></span></span></div>
    <div class="row" style="top:454px"><span class="l">Parkinson's</span><span class="y" style="left:205px">Yes<span class="box"></span></span><span class="n" style="left:241px">No<span class="box"></span></span></div>
    <div class="row" style="top:466px"><span class="l">Radiation to Head/Neck</span><span class="y" style="left:205px">Yes<span class="box"></span></span><span class="n" style="left:241px">No<span class="box"></span></span></div>
    <div class="row" style="top:478px"><span class="l">Schizophrenia</span><span class="y" style="left:205px">Yes<span class="box"></span></span><span class="n" style="left:241px">No<span class="box"></span></span></div>
    <div class="row" style="top:490px"><span class="l">Snoring</span><span class="y" style="left:205px">Yes<span class="box"></span></span><span class="n" style="left:241px">No<span class="box"></span></span></div>
    <div class="row" style="top:502px"><span class="l">Sleep apnea</span><span class="y" style="left:205px">Yes<span class="box"></span></span><span class="n" style="left:241px">No<span class="box"></span></span></div>
    <div class="row" style="top:514px"><span class="l">Stroke</span><span class="y" style="left:205px">Yes<span class="box"></span></span><span class="n" style="left:241px">No<span class="box"></span></span></div>

    <span class="head" style="top:539px">Other</span>
  </div>
  <div class="g" style="left:286px;top:552px;width:229px;height:26px"></div>

  <span class="sign" style="left:34px;top:650px">SIGNATURE</span>
  <div class="line" style="left:81px;top:658px;width:175px"></div>
  <span class="sign" style="left:323px;top:650px">DATE</span>
  <div class="line" style="left:349px;top:658px;width:172px"></div>

  <p class="thanks" style="top:712px">Thank you for the time to complete your medical history form.</p>
  <p class="thanks" style="top:720px">Oral health is linked to overall health and this comprehensive questionnaire will help us to provide you with optimal and safe care.</p>
</section>

</body>
</html>
```